San Francisco Leading Consulting firm - 47Vora Web Design Project

•Create a Web Design
•Uncoded webpage layout design
•2 Pages Design - Homepage + Interior Page

Task Description
Hello, we're looking for a re-design our current website www.47vora-example.com

we have a sample mockup design @

http://47vora.pubtrellis-example.org/

This shows the layout that we like and also a sample of 6 pictures that would change based on where you mouse over..

6 pictures HOME design needs to be included.

SMART
THOUGHTFUL
FLEXIBLE
CREATIVE SERVICES
TECHNICAL SERVICES
PARTNERS

sites we like:

http://www.melvanadvisory-example.com/Home.cfm?id=Home
http://www.plinthworks-example.com/index.html

Our company can be best described as: 100+ employees, cutting-edge, depandable, innovative, strong, smart.

Our Primary focus is: IT Consulting Services and Creative Design services

47Vora LLC is a consulting firm providing creative design, business and technology solutions to both private and public interests.

Established in 1996, 47Vora is a San Francisco based company providing specialists for a range of business needs including:

Creative Design Services
•Print
•Logo Design
•Website Design
•Illustration

and

Business and Technology solutions

•Application Software and Web Development
•Business Process Re-Design (BPR)
•Business/Systems Analysis and Requirement Documentation
•Mentoring and Training
•Network/Hardware Installation Services
•System Design and Architecture
•Vendor Management
•Docuvault Architecture and Implementation

our sample mockup site:

Reason: Due to holiday season, we're not available to work with designers and finilize our design.  

Thank you very much for submitting your design.

We appreciate your time and creativity.   Since, our office is currently closed for holidays, we will be reviewing it in details next week and will make our decision as soon as possible.

It would be great if you could submit any of your changes by Wed next week, so it would be part of our reviews. 

Please see updated wireframe under attachments:  we have some minor updates to our wireframe that we would like you to update your designs, if possible.  

We also encorouge you not to use our standard wireframe and come up with more unique designs.   Everything would be considered when we review your design.

 

Target Market(s)

Creative services and professional services clients, including government agencies

Industry/Entity Type

Business

Requirements
Must have
• Clean, professional look, easy navigation

```html
<!DOCTYPE html>
<html lang="en">
<head>
<meta charset="utf-8">
<title>47Vora – Technical Services</title>
<link rel="stylesheet" href="https://fonts.googleapis.com/css2?family=Mulish:wght@400;600;700&family=Noto+Sans:wght@400;700&display=swap">
<style>
  :root{
    --page-top:#ececec;
    --page-bottom:#f8f8f8;
    --frame:#d9d9d9;
    --panel:#ececec;
    --navy:#1d4566;
    --blue:#1a5a8c;
    --blue-text:#0f5c97;
    --heading:#244f72;
    --ink:#1a1a1a;
    --nav-ink:#333;
    --footer:#2b2b2b;
    --footer-ink:#9a9a9a;
    --footer-light:#bdbdbd;
    --item-bg:#e2e2e2;
  }
  *{box-sizing:border-box;margin:0;padding:0}
  html,body{width:1200px;height:892px;overflow:hidden}
  body{position:relative;background:linear-gradient(var(--page-top),var(--page-bottom) 700px);font-family:"Noto Sans",sans-serif;color:var(--ink)}
  .brand{position:absolute;left:187px;top:22px;display:flex;align-items:center;gap:10px}
  .brand-dot{width:38px;height:38px;border-radius:50%;background:#3a8ec8}
  .brand-name{font-family:"Mulish",sans-serif;font-size:32px;font-weight:400;color:#4a4a4a;letter-spacing:1px}
  .main-nav{position:absolute;right:178px;top:48px;display:flex;align-items:center;font-family:"Mulish",sans-serif;font-size:13px;color:var(--nav-ink)}
  .main-nav a{color:inherit;text-decoration:none;padding:3px 5px}
  .main-nav .sep{padding:0 3px}
  .main-nav .current{background:#dcdcdc;color:var(--blue);font-weight:700;font-size:14px;margin:0 8px;padding:3px 6px}
  .frame{position:absolute;left:177px;top:104px;width:846px;height:635px;background:repeating-linear-gradient(45deg,#dcdcdc 0 2px,#e8e8e8 2px 4px)}
  .panel{position:absolute;left:187px;top:114px;width:826px;height:625px;background:var(--panel)}
  .hero{position:absolute;left:187px;top:114px;width:826px;height:151px;background:linear-gradient(90deg,#1f6ea3,#3b91c6 60%,#62a9d4)}
  .hero-title{position:absolute;left:0;top:0;width:267px;height:47px;background:var(--navy);color:#fff;font-family:"Mulish",sans-serif;font-weight:700;font-size:21px;padding:11px 0 0 29px}
  .hero-copy{position:absolute;left:29px;top:67px;width:330px;color:#fff;font-size:10px;font-weight:700;line-height:12.2px;letter-spacing:.2px}
  .hero-more{position:absolute;left:29px;top:123px;color:#fff;font-size:9.5px;font-weight:700;letter-spacing:.6px}
  .hero-photo{position:absolute;right:0;top:0;width:237px;height:151px;background:linear-gradient(90deg,#6eaed6,#d9dfe4 45%,#f1eeea)}
  .service-list{position:absolute;left:187px;top:291px;width:238px;list-style:none}
  .service-list li{height:33px;margin-bottom:5px;background:repeating-linear-gradient(45deg,#e0e0e0 0 2px,#e9e9e9 2px 4px);font-family:"Mulish",sans-serif;font-weight:700;font-size:13.5px;color:var(--blue-text);padding:7px 0 0 8px}
  .service-list li::before{content:"›";font-size:17px;margin-right:9px;position:relative;top:1px}
  .service-list .active{background:var(--navy);color:#fff}
  .content-title{position:absolute;left:451px;top:296px;font-family:"Mulish",sans-serif;font-weight:700;font-size:20px;color:var(--heading)}
  .content-photo{position:absolute;left:758px;top:331px;width:236px;height:157px;border:1px solid #555;border-radius:8px;background:linear-gradient(120deg,#3b3b3b,#8a8a8a 45%,#dcdcdc)}
  .copy{position:absolute;left:452px;font-size:10.3px;line-height:12.2px;color:var(--ink)}
  .copy p{margin-bottom:12px}
  .copy.narrow{top:332px;width:300px}
  .copy.wide{top:494px;width:545px}
  .site-footer{position:absolute;left:0;top:739px;width:1200px;height:153px;background:var(--footer)}
  .footer-inner{position:absolute;left:177px;top:0;width:846px;height:145px;background:repeating-linear-gradient(45deg,#2e2e2e 0 2px,#333 2px 4px)}
  .testimonial{position:absolute;left:15px;top:17px;width:440px;color:var(--footer-ink);font-size:10.3px;line-height:12px}
  .testimonial h2{font-family:"Mulish",sans-serif;font-size:15px;font-weight:700;color:#a8a8a8;margin-bottom:9px}
  .testimonial .author{margin-top:12px;font-weight:700;letter-spacing:.5px}
  .testimonial .more{position:absolute;right:0;bottom:12px;font-weight:700;letter-spacing:.5px}
  .divider{position:absolute;left:514px;top:24px;width:1px;height:95px;background:#444}
  .contact{position:absolute;right:26px;top:20px;text-align:right;color:var(--footer-light);font-size:10.3px;line-height:11.8px}
  .social{position:absolute;right:26px;top:86px;display:flex;gap:9px}
  .social span{width:25px;height:25px;border-radius:3px;background:#8a8a8a}
  .copyright{position:absolute;right:26px;top:118px;color:var(--footer-light);font-size:10.3px}
</style>
</head>
<body>
  <header>
    <div class="brand"><span class="brand-dot"></span><span class="brand-name">47Vora</span></div>
    <nav class="main-nav">
      <a href="#">Home</a><span class="sep">|</span>
      <a href="#">Company</a>
      <a href="#" class="current">Technical Services</a>
      <a href="#">Creative Services</a><span class="sep">|</span>
      <a href="#">Partners</a><span class="sep">|</span>
      <a href="#">Contact Us</a>
    </nav>
  </header>

  <div class="frame"></div>
  <main class="panel"></main>

  <section class="hero">
    <h1 class="hero-title">Our Technical Services</h1>
    <p class="hero-copy">Lorem Ipsum is simply dummy text of the printing and typesetting industry. Lorem Ipsum has been the industry's standard dummy text ever since the 1500s.</p>
    <a class="hero-more">Read More</a>
    <div class="hero-photo" role="img" aria-label="Photo of a smiling support agent wearing a headset"></div>
  </section>

  <ul class="service-list">
    <li class="active">Business Intelligence Consulting</li>
    <li>Docuvault Consulting</li>
    <li>EDI &amp; SOA Consulting</li>
    <li>Cloud Web Applications</li>
    <li>Dash Board &amp; Reports</li>
    <li>Document Management</li>
    <li>Marketing Collateral</li>
    <li>Packaging</li>
    <li>Books</li>
  </ul>

  <h2 class="content-title">Business Intelligence Consulting:</h2>
  <div class="content-photo" role="img" aria-label="Photo of business consultants reviewing data on a monitor"></div>
  <div class="copy narrow">
    <p>Lorem Ipsum is simply dummy text of the printing and typesetting industry. Lorem Ipsum has been the industry's standard dummy text ever since the 1500s, when an unknown printer took a galley of type and scrambled it to make a type specimen book. It has survived not only five centuries, but also the leap into electronic typesetting, remaining essentially unchanged.</p>
    <p>It was popularised in the 1960s with the release of Typeleaf sheets containing Lorem Ipsum passages, more recently with desktop publishing software like Pressline Composer including versions of Lorem Ipsum.</p>
  </div>
  <div class="copy wide">
    <p>Lorem Ipsum is simply dummy text of the printing and typesetting industry. Lorem Ipsum has been the industry's standard dummy text ever since the 1500s, when an unknown printer took a galley of type and scrambled it to make a type specimen book. It has survived not only five centuries, but also the leap into electronic typesetting, remaining essentially unchanged.</p>
    <p>It was popularised in the 1960s with the release of Typeleaf sheets containing Lorem Ipsum passages, and more recently with desktop publishing software like Pressline Composer including versions of Lorem Ipsum.</p>
  </div>

  <footer class="site-footer">
    <div class="footer-inner">
      <div class="testimonial">
        <h2>Testimonials</h2>
        <p>Now we can start to reap the benefits of current technology, including full vendor support, enhanced financial system functionality, and automation of manual processes. This upgrade was a necessary prerequisite to our full deployment of a strategic systems architecture.....</p>
        <p class="author">Marla Devenish</p>
        <p>Director – IS, Bayview Harbor Authority</p>
        <span class="more">Read More</span>
      </div>
      <div class="divider"></div>
      <address class="contact" style="font-style:normal">
        47Vora, LLC<br>
        2275 Kestrel Avenue, Suite 410<br>
        San Francisco, CA 94107<br>
        Phone: 1-415-555-0142<br>
        Fax: 1-415-555-0198
      </address>
      <div class="social"><span></span><span></span><span></span><span></span></div>
      <p class="copyright">Copyright 2010, 47Vora, LLC All rights reserved</p>
    </div>
  </footer>
</body>
</html>
```